Corvane Card

The logo is the Spanish flag colors I want a vibrant eye catching design with the yellow / red colors over either Navy or white background or black even ,
Would like a 2D feel to the logo with another lighter color logo under it look ,

Contact Information for Business Card

Corvane Flooring
Teodor Vashkin
Main Number
Cell Number
Fax Number

Website on the side of the card somewhere

Font styles to use
Sans Serif

Colors
ec1f27
ffc214

Requirements
Must have
• 2 logos feel one is bolder and the other one underneath very light

```html
<!DOCTYPE html>
<html lang="en">
<head>
<meta charset="utf-8">
<title>Corvane Flooring — Business Card</title>
<link href="https://fonts.googleapis.com/css2?family=Montserrat:wght@700&family=Roboto:wght@400&display=swap" rel="stylesheet">
<style>
  :root {
    --red: #ec1f27;
    --yellow: #ffc214;
    --card: #222222;
    --backdrop: #141414;
    --text-light: #ffffff;
    --divider: #4a4a4a;
  }
  * { margin: 0; padding: 0; box-sizing: border-box; }
  html, body { width: 1200px; height: 1015px; overflow: hidden; }
  body {
    background: radial-gradient(ellipse at 50% 45%, #2c2c2c 0%, var(--backdrop) 75%);
    font-family: "Montserrat", sans-serif;
    position: relative;
  }
  .card {
    position: absolute;
    left: 290px;
    width: 620px;
    height: 354px;
    background: var(--card);
    box-shadow: 0 18px 40px rgba(0,0,0,0.6);
    overflow: hidden;
  }
  .card--front { top: 118px; }
  .card--back { top: 542px; }

  .card__stripe {
    position: absolute;
    left: 0; right: 0; bottom: 0;
    height: 11px;
    background: linear-gradient(90deg, var(--red) 0 46%, var(--yellow) 46% 100%);
  }

  /* Wordmark: one colour, one weight */
  .brand {
    display: flex;
    flex-direction: column;
    align-items: center;
    gap: 14px;
  }
  .brand__square {
    width: 64px; height: 64px;
    background: var(--yellow);
  }
  .brand__name {
    font-family: "Montserrat", sans-serif;
    font-weight: 700;
    color: var(--red);
    text-transform: uppercase;
    text-align: left;
    line-height: 1;
  }
  .brand__primary {
    display: block;
    font-size: 38px;
    letter-spacing: 2px;
  }
  .brand__secondary {
    display: block;
    font-size: 17px;
    letter-spacing: 17px;
    margin-top: 8px;
    padding-left: 46px;
  }

  .card--front .brand {
    position: absolute;
    top: 60px; left: 0; right: 0;
  }
  .card__website {
    position: absolute;
    top: 274px; left: 0; right: 0;
    text-align: center;
    font-family: "Roboto", sans-serif;
    font-size: 15px;
    letter-spacing: 2.5px;
    color: var(--yellow);
  }

  .card--back .brand {
    position: absolute;
    top: 82px; left: 30px;
    width: 290px;
  }
  .brand--compact .brand__square { width: 52px; height: 52px; }
  .brand--compact .brand__primary { font-size: 31px; }
  .brand--compact .brand__secondary {
    font-size: 14px;
    letter-spacing: 13px;
    padding-left: 38px;
    margin-top: 7px;
  }

  .card__divider {
    position: absolute;
    left: 336px; top: 70px;
    width: 1px; height: 190px;
    background: var(--divider);
  }
  .contact {
    position: absolute;
    left: 364px; top: 88px;
  }
  .contact__name {
    font-weight: 700;
    font-size: 23px;
    color: var(--red);
    text-transform: uppercase;
    margin-bottom: 18px;
  }
  .contact__name span { color: var(--yellow); }
  .contact__list { list-style: none; }
  .contact__item {
    display: flex;
    align-items: center;
    gap: 10px;
    font-family: "Roboto", sans-serif;
    font-size: 15px;
    color: var(--text-light);
    margin-bottom: 9px;
  }
  .contact__icon { width: 16px; height: 16px; flex: none; fill: var(--red); }
</style>
</head>
<body>

<section class="card card--front" aria-label="Card front">
  <div class="brand">
    <span class="brand__square"></span>
    <span class="brand__name">
      <span class="brand__primary">Corvane</span>
      <span class="brand__secondary">Flooring</span>
    </span>
  </div>
  <p class="card__website">www.corvaneflooring.example</p>
  <div class="card__stripe"></div>
</section>

<section class="card card--back" aria-label="Card back">
  <div class="brand brand--compact">
    <span class="brand__square"></span>
    <span class="brand__name">
      <span class="brand__primary">Corvane</span>
      <span class="brand__secondary">Flooring</span>
    </span>
  </div>
  <div class="card__divider"></div>
  <div class="contact">
    <h1 class="contact__name">Teodor <span>Vashkin</span></h1>
    <ul class="contact__list">
      <li class="contact__item">
        <svg class="contact__icon" viewBox="0 0 16 16" aria-hidden="true"><path d="M1 6c0-2 3-4 7-4s7 2 7 4v1h-4V5.5H5V7H1z"/><rect x="3" y="8" width="10" height="6" rx="1"/></svg>
        312 408 7751
      </li>
      <li class="contact__item">
        <svg class="contact__icon" viewBox="0 0 16 16" aria-hidden="true"><path d="M4 1h8a1 1 0 0 1 1 1v12a1 1 0 0 1-1 1H4a1 1 0 0 1-1-1V2a1 1 0 0 1 1-1zm1 2v9h6V3z"/></svg>
        312 664 2093
      </li>
      <li class="contact__item">
        <svg class="contact__icon" viewBox="0 0 16 16" aria-hidden="true"><rect x="4" y="1" width="8" height="5"/><rect x="1" y="6" width="14" height="6" rx="1"/><rect x="4" y="11" width="8" height="4"/></svg>
        312 408 7760
      </li>
      <li class="contact__item">
        <svg class="contact__icon" viewBox="0 0 16 16" aria-hidden="true"><path d="M1 3h14v10H1zm1.5 1.5L8 9l5.5-4.5z" fill-rule="evenodd"/></svg>
        info@corvane.example
      </li>
    </ul>
  </div>
  <div class="card__stripe"></div>
</section>

</body>
</html>
```